Restwell/Snoring Business - Requires Website - Australia

We are seeking a simple to maintain website for our sleep business. The health care business provides diagnostic and treatment solutions for snoring, sleep disorders and other respiratory problems.

Ideally, colours to match the company logo (attached).

The page must be built using WORDPRESS.

Ideally site will have a home page outlining the business, with 5 sub pages - being "Diagnosis" "Treatment Options", "Prodcuts", "About Us", "Contact Us"

The site home page should include a large picture on the home page.

The "Treatment Options" and "Diagnosis" pages must include:
Allow for a few pictures with assocaited text, plus space for some embeded youtube videos.

"Prodcuts" page should have the ability to show 3-4 products across the page with text below.. that can include external URL to products

The "About Us" page must include:
1. a Map (google map) to identify the various locations. There are 6 in total.
2. A Section to describe our doctors/staff - allow for a picture and some text

The "Contact Us" page must include:
email form
telephone details

The overall design should have a clean and medical/safe feeling

Target Market(s)

People who snore and those with sleeping and respiratory disorders

Industry/Entity Type

Health Care

Coding

Coded - Design and coding required

Number of Pages Required

5+ page

Colors

Designer to choose colors to be used in the design.

Requirements
Must have
• The page must be built using WORDPRESS.
• Ideally site will have a home page outlining the business, with 5 sub pages - being "Diagnosis" "Treatment Options", "Prodcuts", "About Us", "Contact Us"
• The site home page should include a large picture on the home page.
• The "Treatment Options" and "Diagnosis" pages must include:
• Allow for a few pictures with assocaited text, plus space for some embeded youtube videos.
• "Prodcuts" page should have the ability to show 3-4 products across the page with text below.. that can include external URL to products
• The "About Us" page must include:
• 1. a Map (google map) to identify the various locations. There are 6 in total.
• 2. A Section to describe our doctors/staff - allow for a picture and some text
• The "Contact Us" page must include:
• email form
• telephone details
• Pictures must be licenced or free to use
Nice to have
• Home page pictures showing people sleeping well, snoring or fresh air (landscape) type transition pictures (at least 3).
Should not have
• Not to look cheap
• This is a high end healthcare business, so must look that way

```html
<!DOCTYPE html>
<html lang="en">
<head>
<meta charset="utf-8">
<title>Restwell – Sleep &amp; Respiratory Care</title>
<link rel="stylesheet" href="https://fonts.googleapis.com/css2?family=Roboto+Condensed:wght@400;700&family=Roboto:wght@400;500&family=Open+Sans:wght@400;600&display=swap">
<style>
:root{
  --navy:#0b3f73;
  --navy-dark:#07305a;
  --band:#1d5a93;
  --band-light:#2d6ca6;
  --soft-blue:#9fb6df;
  --ring:#9db3d9;
  --ink:#2b2f36;
  --muted:#555b63;
  --link:#1f6fb8;
  --footer:#f4f5f7;
  --line:#e3e6ea;
  --white:#ffffff;
}
*{box-sizing:border-box;margin:0;padding:0}
html,body{width:1200px;height:2980px;overflow:hidden}
body{position:relative;background:var(--white);font-family:"Open Sans",Arial,sans-serif;color:var(--ink)}
h1,h2,h3,h4{font-weight:400}
.heading{font-family:"Roboto Condensed","Arial Narrow",sans-serif;text-transform:uppercase}
.btn{position:absolute;display:flex;align-items:center;justify-content:center;gap:8px;background:var(--navy);color:var(--white);border-radius:20px;font-family:"Roboto",Arial,sans-serif;font-weight:500;text-transform:uppercase;font-size:13px;letter-spacing:.3px}
.btn .dot{width:12px;height:12px;border-radius:50%;background:var(--white);display:inline-flex;align-items:center;justify-content:center}

/* header */
.site-header{position:absolute;left:0;top:0;width:1200px;height:122px;background:var(--white)}
.brand{position:absolute;left:100px;top:38px;font-family:"Roboto Condensed",sans-serif;font-weight:700;font-size:48px;color:var(--navy);letter-spacing:-.5px}
.header-phone{position:absolute;left:688px;top:28px;font-family:"Roboto",sans-serif;font-size:15px;color:var(--ink);display:flex;align-items:center;gap:10px}
.appt{left:906px;top:20px;width:202px;height:36px;font-size:13px}
.main-nav{position:absolute;top:82px;right:94px;display:flex;gap:26px;font-family:"Roboto",sans-serif;font-size:14px;text-transform:uppercase;color:var(--ink)}
.main-nav .active{color:var(--navy)}

/* hero */
.hero{position:absolute;left:0;top:122px;width:1200px;height:570px;overflow:hidden}
.hero-media{position:absolute;inset:0;background:linear-gradient(100deg,#8e9196 0%,#b9bcc0 30%,#dfe2e4 55%,#e9ebec 75%,#c8cbcf 100%)}
.hero-title{position:absolute;left:98px;top:182px;font-family:"Roboto Condensed",sans-serif;font-weight:700;font-size:52px;color:var(--white);letter-spacing:.5px}
.hero-text{position:absolute;left:98px;top:250px;width:330px;font-size:13px;line-height:20px;color:var(--white)}
.hero-btn{left:98px;top:326px;width:122px;height:34px}
.hero-arrow{position:absolute;top:242px;width:34px;height:34px;border-radius:50%;background:#2a2d31;display:flex;align-items:center;justify-content:center}
.hero-wave{position:absolute;left:0;bottom:0}

/* welcome */
.welcome-photo{position:absolute;left:128px;top:760px;width:320px;height:320px;border-radius:50%;border:4px solid var(--ring);padding:10px;background:var(--white)}
.welcome-photo .fill{width:100%;height:100%;border-radius:50%;background:linear-gradient(135deg,#e8eef3 0%,#c9d7e2 45%,#e6c9a8 80%,#d8b48e 100%)}
.welcome-title{position:absolute;left:502px;top:780px;font-family:"Roboto Condensed",sans-serif;font-size:34px;color:var(--ink)}
.welcome-text{position:absolute;left:502px;top:838px;width:570px;font-size:11.5px;line-height:20px;color:var(--muted)}
.welcome-text p+p{margin-top:12px}
.welcome-btn{left:502px;top:1040px;width:106px;height:32px;font-size:11px}

/* solutions */
.solutions{position:absolute;left:0;top:1166px;width:1200px;height:588px;background:linear-gradient(90deg,var(--band) 0%,var(--band-light) 55%,#1c5990 100%)}
.solutions-title{position:absolute;left:0;width:1200px;top:58px;text-align:center;font-weight:700;font-size:29px;color:var(--white)}
.card{position:absolute;top:142px;width:318px;height:370px;background:#f7f8f9;border-radius:4px;overflow:hidden}
.card-media{position:absolute;left:0;top:0;width:318px;height:196px}
.card-title{position:absolute;left:0;width:318px;top:222px;text-align:center;font-family:"Roboto Condensed",sans-serif;font-size:18px;color:var(--navy)}
.card-text{position:absolute;left:22px;width:274px;top:256px;text-align:center;font-size:11px;line-height:19px;color:var(--muted)}
.card-more{position:absolute;left:0;width:318px;top:334px;text-align:center;font-family:"Roboto",sans-serif;font-size:12px;color:var(--navy);text-transform:uppercase}

/* blog + video */
.section-title{position:absolute;top:1838px;font-family:"Roboto Condensed",sans-serif;font-size:27px;color:var(--ink)}
.post{position:absolute;left:98px;width:546px;height:146px}
.post-thumb{position:absolute;left:0;top:0;width:174px;height:144px}
.post-title{position:absolute;left:196px;top:0;font-family:"Roboto",sans-serif;font-size:15px;color:var(--ink)}
.post-meta{position:absolute;left:196px;top:30px;font-size:10.5px;color:var(--link);text-transform:uppercase}
.post-meta span{color:var(--muted);margin:0 8px}
.post-text{position:absolute;left:196px;top:56px;width:350px;font-size:11px;line-height:20px;color:var(--muted)}
.post-rule{position:absolute;left:196px;bottom:0;width:350px;height:1px;background:var(--line)}
.video{position:absolute;left:698px;top:1894px;width:408px;height:318px;border:1px solid #cfd4d8}
.video-media{position:absolute;inset:0 0 26px 0;background:linear-gradient(120deg,#c9d2d8 0%,#e8ecef 40%,#e9d9c6 70%,#bcc6cc 100%)}
.video-play{position:absolute;left:182px;top:128px}
.video-bar{position:absolute;left:0;bottom:0;width:100%;height:26px;background:#eef0f2}

/* treatment band */
.treatment{position:absolute;left:0;top:2300px;width:1200px;height:340px;background:linear-gradient(90deg,#a8badf 0%,#b6c6e6 50%,#a7b9de 100%)}
.treatment-title{position:absolute;left:0;width:1200px;top:98px;text-align:center;font-weight:700;font-size:32px;color:var(--white)}
.treatment-text{position:absolute;left:156px;width:888px;top:150px;text-align:center;font-size:11.5px;line-height:20px;color:var(--white)}
.treatment-btn{left:540px;top:234px;width:122px;height:34px}

/* footer */
.site-footer{position:absolute;left:0;top:2640px;width:1200px;height:280px;background:var(--footer)}
.footer-brand{position:absolute;left:100px;top:88px;font-family:"Roboto Condensed",sans-serif;font-weight:700;font-size:50px;color:var(--navy)}
.social{position:absolute;left:122px;top:202px;display:flex;gap:10px}
.social span{width:22px;height:22px;border-radius:50%;background:#8a8f95}
.footer-col{position:absolute;top:60px}
.footer-heading{font-family:"Roboto",sans-serif;font-size:16px;color:var(--ink);text-transform:uppercase;margin-bottom:18px}
.contact-item{display:flex;gap:12px;font-size:12px;line-height:18px;color:var(--muted);margin-bottom:16px;width:200px}
.contact-item svg{flex:none;margin-top:2px}
.quick-links{list-style:none;font-size:11.5px;color:var(--muted);line-height:20.5px}
.quick-links li::before{content:"›";margin-right:12px;color:#777}
.newsletter-text{width:286px;font-size:11.5px;line-height:19px;color:var(--muted)}
.newsletter-form{position:absolute;top:90px;left:0;display:flex}
.newsletter-form .field{width:196px;height:44px;background:var(--white);border:1px solid #d5d9dd;font-size:11.5px;color:var(--ink);padding:0 14px;display:flex;align-items:center}
.newsletter-form .submit{width:88px;height:44px;background:var(--navy);color:var(--white);font-family:"Roboto",sans-serif;font-size:12.5px;display:flex;align-items:center;justify-content:center;text-transform:uppercase}
.copyright{position:absolute;left:0;top:2920px;width:1200px;height:60px;border-top:1px solid var(--line);display:flex;align-items:center;justify-content:center;font-size:11.5px;color:var(--muted)}
</style>
</head>
<body>

<header class="site-header">
  <div class="brand">Restwell</div>
  <div class="header-phone">
    <svg width="16" height="16" viewBox="0 0 24 24"><path fill="#555" d="M6.6 10.8a15 15 0 0 0 6.6 6.6l2.2-2.2a1 1 0 0 1 1-.25 11.4 11.4 0 0 0 3.6.57 1 1 0 0 1 1 1V20a1 1 0 0 1-1 1A17 17 0 0 1 3 4a1 1 0 0 1 1-1h3.5a1 1 0 0 1 1 1c0 1.25.2 2.45.57 3.57a1 1 0 0 1-.25 1z"/></svg>
    Phone : 02 5550 1847
  </div>
  <div class="btn appt">Request an Appointment</div>
  <nav class="main-nav">
    <span class="active">Home</span><span>Diagnosis</span><span>Treatment Options</span><span>Products</span><span>About Us</span><span>Contact Us</span>
  </nav>
</header>

<section class="hero">
  <div class="hero-media" role="img" aria-label="Woman stretching happily in a bright room after a good night's sleep"></div>
  <h1 class="hero-title">HEALTH CARE</h1>
  <p class="hero-text">Restful nights begin with a clear diagnosis and a care plan shaped around the way you breathe.</p>
  <div class="btn hero-btn">Read More <span class="dot"><svg width="8" height="8" viewBox="0 0 8 8"><path d="M3 1.5 5.5 4 3 6.5" stroke="#0b3f73" stroke-width="1.5" fill="none"/></svg></span></div>
  <div class="hero-arrow" style="left:26px"><svg width="12" height="12" viewBox="0 0 12 12"><path d="M8 2 4 6l4 4" stroke="#fff" stroke-width="2" fill="none"/></svg></div>
  <div class="hero-arrow" style="left:1124px"><svg width="12" height="12" viewBox="0 0 12 12"><path d="M4 2l4 4-4 4" stroke="#fff" stroke-width="2" fill="none"/></svg></div>
  <svg class="hero-wave" width="1200" height="80" viewBox="0 0 1200 80">
    <path d="M0 20 Q600 110 1200 30 L1200 80 L0 80 Z" fill="#fff"/>
    <path d="M0 20 Q600 110 1200 30" fill="none" stroke="#0b3f73" stroke-width="5"/>
  </svg>
</section>

<section class="welcome">
  <div class="welcome-photo"><div class="fill" role="img" aria-label="Doctor reviewing results on a tablet with a patient"></div></div>
  <h2 class="welcome-title heading">Welcome to Restwell</h2>
  <div class="welcome-text">
    <p>Our clinics bring together sleep physicians, respiratory specialists and friendly support staff who listen first and test carefully. We look at how you sleep, how you breathe and how you feel during the day, then explain every result in plain words. From a first consultation to ongoing follow up, each step is planned to help you rest better and wake with more energy.</p>
    <p>Home and in-clinic studies are available across our locations, with treatment options that fit your needs, your routine and your budget. Ask our team which path suits you.</p>
  </div>
  <div class="btn welcome-btn">Read More <span class="dot"><svg width="8" height="8" viewBox="0 0 8 8"><path d="M3 1.5 5.5 4 3 6.5" stroke="#0b3f73" stroke-width="1.5" fill="none"/></svg></span></div>
</section>

<section class="solutions">
  <h2 class="solutions-title heading">Diagnostic &amp; Treatment Solutions</h2>

  <article class="card" style="left:98px">
    <svg class="card-media" viewBox="0 0 318 196" role="img" aria-label="Man sleeping peacefully on a white pillow">
      <defs><linearGradient id="g1" x1="0" y1="0" x2="1" y2="1"><stop offset="0" stop-color="#d9dbdd"/><stop offset=".6" stop-color="#c9b3a0"/><stop offset="1" stop-color="#eceeef"/></linearGradient></defs>
      <rect width="318" height="196" fill="url(#g1)"/>
      <path d="M0 176 Q159 120 318 176 L318 196 L0 196Z" fill="#f7f8f9"/>
      <path d="M0 176 Q159 120 318 176" fill="none" stroke="#9fb6df" stroke-width="3"/>
    </svg>
    <h3 class="card-title heading">Sleep Disorders</h3>
    <p class="card-text">Testing and care for insomnia, sleep apnoea and restless nights, guided by specialists who explain every step.</p>
    <div class="card-more">Read More ⊙</div>
  </article>

  <article class="card" style="left:442px">
    <svg class="card-media" viewBox="0 0 318 196" role="img" aria-label="Man snoring with airway highlighted">
      <defs><linearGradient id="g2" x1="0" y1="0" x2="1" y2="1"><stop offset="0" stop-color="#e6e8ea"/><stop offset=".5" stop-color="#c89a86"/><stop offset="1" stop-color="#e3e5e7"/></linearGradient></defs>
      <rect width="318" height="196" fill="url(#g2)"/>
      <path d="M0 176 Q159 120 318 176 L318 196 L0 196Z" fill="#f7f8f9"/>
      <path d="M0 176 Q159 120 318 176" fill="none" stroke="#9fb6df" stroke-width="3"/>
    </svg>
    <h3 class="card-title heading">Snoring</h3>
    <p class="card-text">Find the cause of loud or frequent snoring and choose a comfortable treatment that lets the whole household rest.</p>
    <div class="card-more">Read More ⊙</div>
  </article>

  <article class="card" style="left:786px">
    <svg class="card-media" viewBox="0 0 318 196" role="img" aria-label="Older man using an inhaler">
      <defs><linearGradient id="g3" x1="0" y1="0" x2="1" y2="1"><stop offset="0" stop-color="#eef0f1"/><stop offset=".5" stop-color="#b9b6b2"/><stop offset="1" stop-color="#dfe4e6"/></linearGradient></defs>
      <rect width="318" height="196" fill="url(#g3)"/>
      <path d="M0 176 Q159 120 318 176 L318 196 L0 196Z" fill="#f7f8f9"/>
      <path d="M0 176 Q159 120 318 176" fill="none" stroke="#9fb6df" stroke-width="3"/>
    </svg>
    <h3 class="card-title heading">Other Respiratory Problems</h3>
    <p class="card-text">Assessment of breathing problems that affect sleep, with clear advice and ongoing support from our respiratory team.</p>
    <div class="card-more">Read More ⊙</div>
  </article>
</section>

<section class="blog">
  <h2 class="section-title heading" style="left:98px">Latest Blog</h2>

  <article class="post" style="top:1894px">
    <div class="post-thumb" role="img" aria-label="Patient wearing a sleep study mask" style="background:linear-gradient(135deg,#3b3f45,#9aa3ab 60%,#d5d9dc)"></div>
    <h3 class="post-title">Preparing for Your Home Sleep Study</h3>
    <div class="post-meta">3 Minutes Ago<span>/</span>0 Comments</div>
    <p class="post-text">What to expect on the night of a home sleep study, from fitting the sensors to sending the device back.</p>
    <div class="post-rule"></div>
  </article>

  <article class="post" style="top:2066px">
    <div class="post-thumb" role="img" aria-label="Laboratory sample tubes in a blue rack" style="background:linear-gradient(135deg,#e9eef3,#c9d4df 50%,#3f78c4)"></div>
    <h3 class="post-title">Understanding Your Sleep Test Results</h3>
    <div class="post-meta">3 Minutes Ago<span>/</span>0 Comments</div>
    <p class="post-text">How simple blood and breathing tests help our doctors build a complete view of your sleep health.</p>
    <div class="post-rule"></div>
  </article>

  <h2 class="section-title heading" style="left:698px">Diagnostic Techniques</h2>
  <div class="video">
    <div class="video-media" role="img" aria-label="Clinician performing an ultrasound on a patient"></div>
    <svg class="video-play" width="46" height="46" viewBox="0 0 46 46"><circle cx="23" cy="23" r="21" fill="#0b3f73" stroke="#fff" stroke-width="3"/><path d="M18 14l13 9-13 9z" fill="#9a4fc7"/></svg>
    <svg class="video-bar" viewBox="0 0 408 26">
      <path d="M10 8l7 5-7 5z" fill="#333"/>
      <text x="30" y="17" font-family="Open Sans,sans-serif" font-size="8" fill="#555">0:00/0:23</text>
      <rect x="116" y="12" width="200" height="3" fill="#c9ccd0"/>
      <rect x="116" y="12" width="60" height="3" fill="#c24d3c"/>
      <path d="M340 10h3l4-3v12l-4-3h-3z" fill="#333"/>
      <rect x="354" y="12" width="42" height="3" fill="#c24d3c"/>
    </svg>
  </div>
</section>

<section class="treatment">
  <div role="img" aria-label="Woman relaxing in a bright room" style="position:absolute;inset:0;background:radial-gradient(ellipse at 75% 40%,rgba(255,255,255,.25),transparent 60%)"></div>
  <h2 class="treatment-title heading">Treatment Options</h2>
  <p class="treatment-text">Snoring and sleep apnoea can often be managed with comfortable, modern therapies. Our team explains CPAP, custom oral devices, positional aids and lifestyle changes, then helps you choose the option that suits your sleep, your health and your daily routine.</p>
  <div class="btn treatment-btn">Read More <span class="dot"><svg width="8" height="8" viewBox="0 0 8 8"><path d="M3 1.5 5.5 4 3 6.5" stroke="#0b3f73" stroke-width="1.5" fill="none"/></svg></span></div>
</section>

<footer class="site-footer">
  <div class="footer-brand">Restwell</div>
  <div class="social"><span></span><span></span><span></span><span></span></div>

  <div class="footer-col" style="left:358px">
    <h4 class="footer-heading">Contacts Us</h4>
    <div class="contact-item"><svg width="12" height="14" viewBox="0 0 12 14"><path d="M6 0a5 5 0 0 0-5 5c0 4 5 9 5 9s5-5 5-9a5 5 0 0 0-5-5zm0 7a2 2 0 1 1 0-4 2 2 0 0 1 0 4z" fill="#999"/></svg><span>Restwell, 48 Harbour Lane, New South Wales Australia</span></div>
    <div class="contact-item"><svg width="12" height="12" viewBox="0 0 24 24"><path fill="#999" d="M6.6 10.8a15 15 0 0 0 6.6 6.6l2.2-2.2a1 1 0 0 1 1-.25 11.4 11.4 0 0 0 3.6.57 1 1 0 0 1 1 1V20a1 1 0 0 1-1 1A17 17 0 0 1 3 4a1 1 0 0 1 1-1h3.5a1 1 0 0 1 1 1c0 1.25.2 2.45.57 3.57a1 1 0 0 1-.25 1z"/></svg><span>Phone: (02) 5550 1848</span></div>
    <div class="contact-item"><svg width="12" height="10" viewBox="0 0 12 10"><rect x=".5" y=".5" width="11" height="9" fill="none" stroke="#999"/><path d="M.5.5 6 5l5.5-4.5" fill="none" stroke="#999"/></svg><span>Email: info@restwell-sleep.com</span></div>
  </div>

  <div class="footer-col" style="left:632px">
    <h4 class="footer-heading">Quick Links</h4>
    <ul class="quick-links"><li>Home</li><li>About us</li><li>Diagnosis</li><li>blog</li><li>Treatment Options</li><li>Contact</li></ul>
  </div>

  <div class="footer-col" style="left:822px">
    <h4 class="footer-heading">Sign Up for Newsletter</h4>
    <p class="newsletter-text">Sleep tips, clinic news and new treatment options delivered to your inbox.</p>
    <div class="newsletter-form"><div class="field">Enter Name</div><div class="submit">Subscribe</div></div>
  </div>
</footer>

<div class="copyright">©2017 Restwell .. All Rights Reserved.</div>

</body>
</html>
```